QAMBRO THERAPEUTICS

physical therapy company. need a flashy image and named logo, website link, that I can also use on Letterhead and business cards. Clean, sharp, modern, eye catching. 3 colors? Some shine. Needs to stand out and not be trendy or too much cursive . Androgynous image of a human body is ok. A spine included is ok. Prefer lines to curves for font types. Warm colors but strong impact. Will need to have some contact info and border mission statement on it.
Updates

Target Market(s)

Target market is large corporations, wealthy individuals, medical doctors

Industry/Entity Type

Medical, physical therapy

Contact Information for Business Card

Name, Owner, phone, email, and website

Colors
0054AA
0677BA
7BADD7
CADEEF
E8F1F8

Requirements
Must have
• See above- something about BALANCE, wellness, strength etc
Nice to have
• Contrast, depth
Should not have
• No cursive

```html
<!DOCTYPE html>
<html lang="en">
<head>
<meta charset="utf-8">
<title>Qambro Therapeutics – Business Card</title>
<link href="https://fonts.googleapis.com/css2?family=Montserrat:wght@600;700&family=Poppins:wght@400;500&display=swap" rel="stylesheet">
<style>
  :root {
    --blue-deep: #0054AA;
    --blue-mid: #0677BA;
    --blue-soft: #7BADD7;
    --blue-pale: #CADEEF;
    --blue-mist: #E8F1F8;
    --ink: #1d1d1f;
    --white: #ffffff;
    --backdrop: #eef1f5;
  }
  * { box-sizing: border-box; margin: 0; padding: 0; }
  html, body {
    width: 1200px; height: 900px; overflow: hidden;
    background: var(--backdrop);
  }
  .canvas {
    position: relative; width: 1200px; height: 900px;
    display: flex; flex-direction: column; align-items: center; justify-content: center; gap: 46px;
  }
  .card {
    position: relative; width: 660px; height: 377px; overflow: hidden;
    box-shadow: 0 10px 28px rgba(0, 40, 90, 0.18);
  }
  /* Front */
  .card-front {
    background: linear-gradient(120deg, #0a4fa3 0%, var(--blue-deep) 55%, #0558ad 100%);
  }
  .front-artwork {
    position: absolute; left: 0; top: 0; width: 74%; height: 100%;
    background:
      radial-gradient(ellipse 30% 55% at 62% 48%, rgba(202, 222, 239, 0.55), transparent 70%),
      radial-gradient(ellipse 26% 50% at 40% 52%, rgba(123, 173, 215, 0.45), transparent 70%),
      radial-gradient(ellipse 24% 48% at 20% 55%, rgba(123, 173, 215, 0.35), transparent 72%),
      radial-gradient(circle at 12% 80%, rgba(6, 119, 186, 0.5), transparent 40%);
  }
  .front-brand {
    position: absolute; left: 26%; top: 56%;
    font-family: "Montserrat", sans-serif; font-weight: 700;
    font-size: 33px; letter-spacing: 0.5px; color: var(--white);
    white-space: nowrap;
  }
  /* Back */
  .card-back { background: var(--white); }
  .back-wave { position: absolute; inset: 0; }
  .holder {
    position: absolute; left: 7%; top: 17%;
  }
  .holder-name {
    font-family: "Montserrat", sans-serif; font-weight: 700;
    font-size: 21px; color: var(--blue-deep); letter-spacing: 0.3px;
  }
  .holder-role {
    font-family: "Poppins", sans-serif; font-weight: 400;
    font-size: 15px; color: var(--ink); margin-top: -2px;
  }
  .back-brand {
    position: absolute; right: 5%; top: 26%;
    font-family: "Montserrat", sans-serif; font-weight: 700;
    font-size: 26px; color: var(--blue-deep); white-space: nowrap;
  }
  .contact {
    position: absolute; left: 20%; top: 52%;
    list-style: none;
    font-family: "Poppins", sans-serif; font-size: 18px; color: var(--ink);
  }
  .contact li { display: flex; align-items: center; gap: 9px; line-height: 1.45; }
  .contact svg { width: 17px; height: 17px; fill: var(--blue-deep); flex: none; }
  .back-web {
    position: absolute; right: 6%; bottom: 11%;
    font-family: "Poppins", sans-serif; font-size: 16px; color: var(--white);
  }
</style>
</head>
<body>
<main class="canvas">
  <section class="card card-front">
    <div class="front-artwork" role="img" aria-label="Translucent running human figures shown as skeleton, muscle and body layers on a glowing blue background"></div>
    <h1 class="front-brand">QAMBRO THERAPEUTICS</h1>
  </section>

  <section class="card card-back">
    <svg class="back-wave" viewBox="0 0 660 377" preserveAspectRatio="none" aria-hidden="true">
      <path d="M0,298 C220,296 390,270 490,212 C560,178 620,162 660,156 L660,377 L0,377 Z" fill="var(--blue-mid)"/>
      <path d="M0,320 C220,318 390,286 495,222 C565,182 622,166 660,162 L660,377 L0,377 Z" fill="var(--white)"/>
      <path d="M0,325 C220,323 390,291 498,227 C568,186 624,170 660,166 L660,377 L0,377 Z" fill="var(--blue-deep)"/>
    </svg>
    <div class="holder">
      <p class="holder-name">DANIEL MORROW</p>
      <p class="holder-role">Managing Director</p>
    </div>
    <p class="back-brand">QAMBRO THERAPEUTICS</p>
    <ul class="contact">
      <li>
        <svg viewBox="0 0 24 24" aria-hidden="true"><path d="M6.6 10.8a15.1 15.1 0 0 0 6.6 6.6l2.2-2.2a1 1 0 0 1 1-.25 11.4 11.4 0 0 0 3.6.57 1 1 0 0 1 1 1V20a1 1 0 0 1-1 1A17 17 0 0 1 3 4a1 1 0 0 1 1-1h3.5a1 1 0 0 1 1 1c0 1.250.2 2.46.57 3.6a1 1 0 0 1-.25 1z"/></svg>
        044-321 654 987
      </li>
      <li>
        <svg viewBox="0 0 24 24" aria-hidden="true"><path d="M2 5h20v14H2z M3.5 6.5 12 13l8.5-6.5" fill="var(--blue-deep)" stroke="var(--white)" stroke-width="1.4"/></svg>
        hello@qambro.com
      </li>
    </ul>
    <p class="back-web">www.qambrotherapy.com</p>
  </section>
</main>
</body>
</html>
```